Harlow Creek Church Invite Card

We are a vibrant multigenerational church outside of Raleigh, NC and are wanting a 'church invite card' that we can encourage our members to carry with them so that they can invite their friends to church.

These cards should have a modern feel (see http://brightmosaic.com/neat-card-ideas/ for the feel we are going for), match the branding of our website (www.harlowcreek.org) and include the following information on the back:

Service Times: Sunday @ 8:30 AM and 11:00 AM (Main Focus)
Website: www.harlowcreek.org (Main Focus)
Social Media: (You can simply use the icons for these if desired)
www.facebook.com/harlowcreekchurch
www.instagram.com/harlowcreekchurch
www.youtube.com/harlowcreekyouth
Address: 2847 Tamsin Parkway Ashgrove, NC 27594 (Not a main focus)
Phone: (919) 482-7093 (Not a main focus)

The front should simply say 'We look forward to meeting you!'

Logos: Attached you will find the necessary logos for this project.

Fonts and Colors: Here are the specific colors (See HCC_Website_Color_Palette.pdf) and fonts that are used on our website.
Pacifico
Helvetica
Open Sans Regular

Target Market(s)

Friends of our congregation

Industry/Entity Type

Church

Contact Information for Business Card

We will likely print through Lantern Printworks. The details of what they need can be found here: http://www.lanternprintworks.com/items/calling-card

Font styles to use
Other font styles liked:
• Pacifico, Helvetica, Open Sans Regular, Bebas Nue

Colors
0592cd
34a7d8
85cae6
cee9f5
0455a3
3176b5
85acd3
cfdfed

Requirements
Must have
• Sleek, eye catching design
Nice to have
• Rounded Corners, Our social media sites (CH, Snap and ClipHarbor)

```html
<!DOCTYPE html>
<html lang="en">
<head>
<meta charset="utf-8">
<title>Harlow Creek Church Invite Card</title>
<link href="https://fonts.googleapis.com/css2?family=Courgette&family=Open+Sans:wght@400;600;700&display=swap" rel="stylesheet">
<style>
  :root {
    --backdrop: #2b2b2d;
    --card-white: #ffffff;
    --ink: #111111;
    --brand-blue: #1a6bb8;
    --bright-blue: #0592cd;
    --strip-grey: #b4b4b4;
    --soft-text: #e8e8e8;
  }
  html, body {
    margin: 0;
    padding: 0;
    width: 1200px;
    height: 900px;
    overflow: hidden;
    background: var(--backdrop);
    font-family: "Open Sans", Helvetica, Arial, sans-serif;
  }
  .canvas {
    position: relative;
    width: 1200px;
    height: 900px;
  }
  .card {
    position: absolute;
    width: 680px;
    height: 388px;
    border-radius: 24px;
    background: var(--card-white);
    overflow: hidden;
  }
  .card--front { left: 110px; top: 40px; }
  .card--back { left: 410px; top: 472px; }

  /* Front */
  .greeting-band {
    position: absolute;
    left: 50%;
    top: 120px;
    transform: translateX(-50%);
    height: 46px;
    padding: 0 20px;
    background: var(--ink);
    color: var(--card-white);
    font-family: "Courgette", cursive;
    font-size: 26px;
    line-height: 46px;
    white-space: nowrap;
    letter-spacing: 1px;
  }
  .church-name {
    position: absolute;
    margin: 0;
    font-family: "Open Sans", Helvetica, Arial, sans-serif;
    font-weight: 700;
    color: var(--ink);
    text-transform: uppercase;
    letter-spacing: 1px;
    white-space: nowrap;
  }
  .card--front .church-name {
    left: 0;
    width: 680px;
    text-align: center;
    top: 190px;
    font-size: 32px;
  }
  .social-list {
    position: absolute;
    right: 26px;
    bottom: 28px;
    display: flex;
    gap: 14px;
    margin: 0;
    padding: 0;
    list-style: none;
  }
  .social-item {
    display: flex;
    align-items: center;
    gap: 5px;
    font-size: 11px;
    font-weight: 600;
    color: var(--brand-blue);
  }
  .social-item::before {
    content: "";
    width: 12px;
    height: 12px;
    background: var(--brand-blue);
    border-radius: 2px;
  }

  /* Back */
  .divider-art {
    position: absolute;
    inset: 0;
  }
  .service-band {
    position: absolute;
    left: 0;
    top: 64px;
    width: 430px;
    height: 34px;
    display: flex;
    align-items: center;
  }
  .service-band__strip {
    width: 34px;
    height: 100%;
    background: var(--strip-grey);
  }
  .service-band__text {
    flex: 1;
    height: 100%;
    background: var(--ink);
    color: var(--soft-text);
    font-size: 16px;
    line-height: 34px;
    padding-left: 12px;
    white-space: nowrap;
  }
  .accent { color: var(--brand-blue); font-weight: 600; }
  .accent-bright { color: var(--bright-blue); font-weight: 600; }
  .card--back .church-name {
    left: 44px;
    top: 146px;
    font-size: 24px;
  }
  .contact {
    position: absolute;
    right: 22px;
    top: 150px;
    text-align: right;
    color: var(--soft-text);
    font-size: 13px;
    font-style: normal;
    line-height: 1.45;
  }
  .contact__name {
    margin: 0 0 6px;
    color: var(--brand-blue);
    font-size: 22px;
    font-weight: 700;
    letter-spacing: 0.5px;
  }
  .contact p { margin: 0; }
  .contact__line {
    display: flex;
    align-items: center;
    justify-content: flex-end;
    gap: 6px;
  }
  .contact__web .accent { font-weight: 400; }
</style>
</head>
<body>
<main class="canvas">

  <section class="card card--front" aria-label="Invite card front">
    <div class="greeting-band">We look forward to meeting you</div>
    <h1 class="church-name">Harlow Creek Church</h1>
    <ul class="social-list">
      <li class="social-item">Chatterly</li>
      <li class="social-item">Snapwell</li>
      <li class="social-item">Chirpline</li>
    </ul>
  </section>

  <section class="card card--back" aria-label="Invite card back">
    <svg class="divider-art" width="680" height="388" viewBox="0 0 680 388" aria-hidden="true">
      <path d="M460 0 C 380 110, 500 260, 360 388 L680 388 L680 0 Z" fill="#111111"/>
      <path d="M460 0 C 380 110, 500 260, 360 388" fill="none" stroke="#1a6bb8" stroke-width="16" stroke-linecap="round"/>
    </svg>

    <div class="service-band">
      <span class="service-band__strip"></span>
      <span class="service-band__text"><span class="accent">SERVICE TIMES:</span> Sunday @ <span class="accent-bright">8:30</span> AM &amp; <span class="accent-bright">11:00</span> AM</span>
    </div>

    <h2 class="church-name">Harlow Creek Church</h2>

    <address class="contact">
      <h3 class="contact__name">DANIEL REYES</h3>
      <p>2847 Tamsin</p>
      <p>Parkway Ashgrove, NC 27594</p>
      <p class="contact__line"><span>(919) 482-7093</span>
        <svg width="11" height="11" viewBox="0 0 24 24" aria-hidden="true"><path fill="#1a6bb8" d="M6.6 10.8a15 15 0 0 0 6.6 6.6l2.2-2.2a1 1 0 0 1 1-.25 11.4 11.4 0 0 0 3.6.6 1 1 0 0 1 1 1V20a1 1 0 0 1-1 1A17 17 0 0 1 3 4a1 1 0 0 1 1-1h3.5a1 1 0 0 1 1 1c0 1.25.2 2.45.6 3.6a1 1 0 0 1-.25 1z"/></svg>
      </p>
      <p class="contact__line contact__web"><span>www.<span class="accent">harlowcreek</span>.org</span>
        <svg width="11" height="11" viewBox="0 0 24 24" aria-hidden="true"><circle cx="12" cy="12" r="9" fill="none" stroke="#1a6bb8" stroke-width="2.5"/><path d="M3 12h18M12 3c3 3 3 15 0 18M12 3c-3 3-3 15 0 18" fill="none" stroke="#1a6bb8" stroke-width="1.8"/></svg>
      </p>
    </address>
  </section>

</main>
</body>
</html>
```